Business Cards

Need business card design that I can update for new employees and details. Needs to incorporate our logo, be bright and fun (in line with tourism and holidays)
Would like a Map of Western Australia on the front with locations all the caravan parks we own (just purchased Tom Price so please include that as well as others listed on our website).
Target Market(s)
Famillies
Contact Information for Business Card
5 Cards -
Neil Perrow (Director) e: perrow@wattlebay.com.au p: 0491 570 156
Mira Perrow (Director) e: perrow@wattlebay.com.au p: 0491 570 157
Owen Halvey (General Manager) e: halvey@wattlebay.com.au p: 0491 570 158
Helen Halvey (General Manager) e: halvey@wattlebay.com.au p: 0491 570 159
Colin Danby (Training and Operations Manager) - e: danby@wattlebay.com.au p:0491 570 110
Colors
Look and feel

```html
<!DOCTYPE html>
<html lang="en">
<head>
<meta charset="utf-8">
<title>Wattlebay Tourist Parks – Business Cards</title>
<link rel="stylesheet" href="https://fonts.googleapis.com/css2?family=Cormorant+Garamond:wght@500;600&family=Open+Sans:wght@400;600&display=swap">
<style>
  :root {
    --bg: #e9ecec;
    --paper: #f4f4f3;
    --ink: #4a4a4a;
    --ink-soft: #6b6b6b;
    --sea: #3dbcc7;
    --sea-green: #6dbfae;
    --white: #ffffff;
    --shadow: 0 10px 30px rgba(0,0,0,.18);
  }
  * { margin: 0; padding: 0; box-sizing: border-box; }
  html, body { width: 1200px; height: 886px; overflow: hidden; background: var(--bg); }
  .sheet {
    width: 1200px; height: 886px;
    display: flex; align-items: center; justify-content: center; gap: 60px;
  }
  .card {
    position: relative;
    width: 520px; height: 297px;
    box-shadow: var(--shadow);
    overflow: hidden;
  }

  /* Front */
  .card--front { background: var(--paper); }
  .brand {
    position: absolute; left: 0; right: 0; top: 92px;
    display: flex; align-items: center; justify-content: center; gap: 16px;
  }
  .brand__mark { width: 46px; height: 46px; background: var(--sea); }
  .brand__text { font-family: "Cormorant Garamond", serif; font-weight: 600; color: var(--ink); }
  .brand__name { font-size: 38px; letter-spacing: 5px; line-height: 1; }
  .brand__tag { font-size: 14px; letter-spacing: 6px; margin-top: 6px; padding-left: 40px; }
  .front__url {
    position: absolute; left: 0; right: 0; bottom: 44px; text-align: center;
    font-family: "Open Sans", sans-serif; font-size: 13px; letter-spacing: 3px; color: var(--ink);
  }

  /* Back */
  .card--back { background: var(--sea); }
  .back__waves { position: absolute; inset: 0; }
  .back__brand {
    position: absolute; right: 34px; top: 34px; text-align: right;
    font-family: "Cormorant Garamond", serif; font-weight: 600; color: var(--white);
  }
  .back__brand .brand__name { font-size: 32px; letter-spacing: 4px; }
  .back__brand .brand__tag { font-size: 12px; letter-spacing: 5px; padding-left: 0; }
  .contact {
    position: absolute; left: 34px; bottom: 34px; color: var(--white);
  }
  .contact__name {
    font-family: "Cormorant Garamond", serif; font-weight: 600;
    font-size: 22px; letter-spacing: 1px; text-transform: uppercase;
  }
  .contact__role {
    font-family: "Cormorant Garamond", serif; font-weight: 600;
    font-size: 15px; letter-spacing: 1px; text-transform: uppercase; margin-bottom: 12px;
  }
  .contact__list { list-style: none; font-family: "Open Sans", sans-serif; font-size: 13px; line-height: 1.55; }
  .contact__list li { display: flex; align-items: center; gap: 8px; }
  .contact__icon { width: 12px; height: 12px; flex: none; }
</style>
</head>
<body>
<main class="sheet">

  <section class="card card--front">
    <div class="brand">
      <span class="brand__mark"></span>
      <div class="brand__text">
        <div class="brand__name">WATTLEBAY</div>
        <div class="brand__tag">TOURIST PARKS</div>
      </div>
    </div>
    <p class="front__url">www.wattlebay.com.au</p>
  </section>

  <section class="card card--back">
    <svg class="back__waves" viewBox="0 0 520 297" preserveAspectRatio="none" aria-hidden="true">
      <path d="M0 70 C120 60 230 110 300 297 L0 297 Z" fill="var(--sea-green)"/>
      <path d="M0 70 C120 60 230 110 300 297" fill="none" stroke="var(--white)" stroke-width="14"/>
    </svg>

    <div class="back__brand">
      <div class="brand__name">WATTLEBAY</div>
      <div class="brand__tag">TOURIST PARKS</div>
    </div>

    <div class="contact">
      <h1 class="contact__name">Neil Perrow</h1>
      <p class="contact__role">Director</p>
      <ul class="contact__list">
        <li>
          <svg class="contact__icon" viewBox="0 0 12 12"><path d="M2.5 1 L4.5 1 L5 3.5 L3.8 4.5 C4.5 6 6 7.5 7.5 8.2 L8.5 7 L11 7.5 L11 9.5 C11 10.3 10.3 11 9.5 11 C5 11 1 7 1 2.5 C1 1.7 1.7 1 2.5 1 Z" fill="var(--white)"/></svg>
          0491 570 156
        </li>
        <li>
          <svg class="contact__icon" viewBox="0 0 12 12"><rect x="0.5" y="2" width="11" height="8" fill="var(--white)"/><path d="M0.5 2 L6 6.5 L11.5 2" fill="none" stroke="var(--sea-green)" stroke-width="1"/></svg>
          perrow@wattlebay.com.au
        </li>
        <li>
          <svg class="contact__icon" viewBox="0 0 12 12"><circle cx="6" cy="6" r="5.5" fill="var(--white)"/><path d="M0.5 6 H11.5 M6 0.5 C3 3.5 3 8.5 6 11.5 M6 0.5 C9 3.5 9 8.5 6 11.5" fill="none" stroke="var(--sea-green)" stroke-width="0.8"/></svg>
          www.wattlebay.com.au
        </li>
      </ul>
    </div>
  </section>

</main>
</body>
</html>
```